Groovanta - A Tasty Blend of R'n'B, Funk & Soul

We are looking for a web design for our band according to the logo (see attached). Logo and Slogan will stay, the backrground of the logo may change. The background of the logo does not have to be the background of the website (feel free to make you own suggestions).

To get some impressions about the band, you can take a look here: https://www.examplebook.test/groovantaberlin

You can also find a songlist in the attachment.

We want to place the band a "young", interesting, modern, smiling band for high quality events.

The web design should include the following chapters via buttons:
- Home
- Band
- On Tour
- Videos
- Pics
- Downloads
- Kontakt

Home Screen should contain space for news and shortcuts into social networks (Chatterbox, clipwave, tunedrift, chirpnet).

Looking forward for your ideas! Happy designing! :-)

Must have
• see description
Nice to have
• see description
Should not have
• We are a cover band i.e. we do not sell albums. So we don't need such a category in the design.

```html
<!DOCTYPE html>
<html lang="en">
<head>
<meta charset="utf-8">
<title>Groovanta - A Tasty Blend of R'n'B, Funk &amp; Soul</title>
<link rel="stylesheet" href="https://fonts.googleapis.com/css2?family=Raleway:wght@500;600;700;800&family=Open+Sans:wght@400;600;700&display=swap">
<style>
:root{
  --bg:#0c0c0c;
  --bg-glow:#1c1c1c;
  --card:#050505;
  --footer:#181818;
  --red:#e8353a;
  --red-dark:#c8242a;
  --yellow:#fcc930;
  --heading-yellow:#f6c232;
  --rose:#ee4d55;
  --violet:#b13ec2;
  --orange:#f79420;
  --white:#ffffff;
  --muted:#c9c9c9;
  --orange-dot:#f7931e;
}
*{margin:0;padding:0;box-sizing:border-box}
html,body{width:1126px;height:1200px;overflow:hidden}
body{
  position:relative;
  background:radial-gradient(ellipse at 50% 40%,var(--bg-glow) 0%,var(--bg) 60%);
  color:var(--white);
  font-family:"Open Sans",sans-serif;
}
.brand{position:absolute;left:190px;top:30px}
.brand-name{
  font-family:"Raleway",sans-serif;font-weight:800;font-size:44px;
  color:var(--orange);letter-spacing:-0.5px;line-height:50px;
}
.brand-tagline{
  font-family:"Raleway",sans-serif;font-weight:500;font-size:8.5px;
  letter-spacing:1.6px;color:var(--muted);text-transform:uppercase;margin-top:4px;
}
.main-nav{
  position:absolute;left:190px;top:109px;width:746px;height:42px;
  background:linear-gradient(var(--red),var(--red-dark));
  display:grid;grid-template-columns:97px 90px 114px 98px 84px 139px 124px;
}
.main-nav a{
  display:flex;align-items:center;justify-content:center;
  font-family:"Raleway",sans-serif;font-weight:700;font-size:13px;
  color:var(--white);text-decoration:none;
  border-right:1px solid rgba(0,0,0,.18);
}
.main-nav a:last-child{border-right:none}
.hero{position:absolute;left:190px;top:151px;width:746px;height:342px}
.hero svg{display:block}
.slider-dots{position:absolute;left:339px;top:313px;display:flex;gap:4px}
.slider-dots span{width:13px;height:13px;border-radius:50%;background:var(--white)}
.slider-dots span.active{background:var(--orange-dot)}
.about{position:absolute;left:190px;top:540px;width:746px;text-align:center}
.about h1{
  font-family:"Raleway",sans-serif;font-weight:700;font-size:25px;
  color:var(--heading-yellow);letter-spacing:1.5px;
}
.about-lead{
  font-family:"Raleway",sans-serif;font-weight:500;font-size:12.6px;
  line-height:19px;margin:12px 20px 0;
}
.about-body{font-size:9.6px;line-height:19px;margin:5px 28px 0}
.btn{
  display:inline-block;font-family:"Raleway",sans-serif;font-weight:700;
  text-transform:uppercase;color:var(--white);text-decoration:none;
}
.btn-about{
  background:var(--yellow);color:#2a2a2a;font-size:11.5px;
  width:110px;height:31px;line-height:31px;margin-top:12px;
}
.features{
  position:absolute;left:190px;top:762px;width:746px;
  display:grid;grid-template-columns:repeat(3,240px);gap:13px;
}
.feature{background:var(--card);height:256px;text-align:center}
.feature-media{height:121px;position:relative}
.feature-media svg{display:block}
.feature h2{
  font-family:"Raleway",sans-serif;font-weight:600;font-size:17px;
  letter-spacing:1px;margin-top:17px;
}
.feature p{font-size:8.6px;line-height:12.8px;color:var(--muted);margin:6px 18px 0}
.feature .btn{font-size:8.5px;width:87px;height:24px;line-height:24px;margin-top:9px}
.feature-band h2{color:var(--rose)} .feature-band .btn{background:var(--rose)}
.feature-videos h2{color:var(--violet)} .feature-videos .btn{background:var(--violet)}
.feature-gallery h2{color:var(--orange)} .feature-gallery .btn{background:var(--orange)}
.site-footer{position:absolute;left:0;top:1071px;width:1126px;height:129px;background:var(--footer)}
.footer-nav{
  position:absolute;left:200px;top:33px;
  font-family:"Raleway",sans-serif;font-weight:700;font-size:12.5px;
}
.footer-nav a{color:var(--white);text-decoration:none}
.footer-nav .sep{margin:0 6px}
.copyright{position:absolute;left:200px;top:59px;font-size:9.6px;color:var(--muted)}
.social{position:absolute;right:190px;top:30px;display:flex;gap:8px}
.social a{
  font-family:"Open Sans",sans-serif;font-weight:600;font-size:9px;
  color:var(--white);text-decoration:none;display:flex;align-items:center;gap:3px;
}
.social a::before{content:"";width:9px;height:9px;background:var(--white);border-radius:2px}
</style>
</head>
<body>
<header class="brand">
  <div class="brand-name">Groovanta</div>
  <div class="brand-tagline">A tasty blend of R&amp;B, funk and soul</div>
</header>

<nav class="main-nav">
  <a href="#">HOME</a><a href="#">BAND</a><a href="#">ON TOUR</a><a href="#">VIDEOS</a><a href="#">PICS</a><a href="#">DOWNLOADS</a><a href="#">KONTAKT</a>
</nav>

<section class="hero">
  <svg width="746" height="342" role="img" aria-label="Stage photos: a guitarist in a red shirt and a singer at a microphone">
    <defs>
      <linearGradient id="heroLeft" x1="0" y1="0" x2="1" y2="1">
        <stop offset="0" stop-color="#3a1210"/><stop offset=".5" stop-color="#8a2418"/><stop offset="1" stop-color="#2a0b08"/>
      </linearGradient>
      <linearGradient id="heroRight" x1="0" y1="0" x2="1" y2="1">
        <stop offset="0" stop-color="#2a1a12"/><stop offset=".5" stop-color="#1a1410"/><stop offset="1" stop-color="#6a3a20"/>
      </linearGradient>
    </defs>
    <polygon points="0,0 423,0 350,342 0,342" fill="url(#heroLeft)"/>
    <polygon points="423,0 746,0 746,342 350,342" fill="url(#heroRight)"/>
  </svg>
  <div class="slider-dots"><span class="active"></span><span></span><span></span><span></span></div>
</section>

<section class="about">
  <h1>LITTLE ABOUT GROOVANTA</h1>
  <p class="about-lead">Morbi ornare gravida elit Integer congue augue et malesuada iaculis ipsum dui aliquet felis at cursus magna nisl nec elit Praesent elementum elit at tellus nec ultricies sit amet porttitor mattis enim</p>
  <p class="about-body">In massa libero interdum nec interdum vel blandit sed nulla In ullamcorper est eget tempor cursus neque mi consectetuer mi a ultricies massa est sed nisl Class aptent taciti sociosqu ad litora torquent per conubia nostra per inceptos hymenaeos Proin nulla arcu nonummy luctus dictum eget fermentum et lorem&nbsp; Sed porta Suspendisse quam leo molestie sed luctus quis feugiat in pede Fusce tellus Sed</p>
  <a class="btn btn-about" href="#">LEARN MORE</a>
</section>

<section class="features">
  <article class="feature feature-band">
    <div class="feature-media">
      <svg width="240" height="121" role="img" aria-label="Drummer playing a green-lit drum kit">
        <defs><linearGradient id="mediaBand" x1="0" y1="0" x2="0" y2="1"><stop offset="0" stop-color="#0b0f0a"/><stop offset="1" stop-color="#1d4a22"/></linearGradient></defs>
        <rect width="240" height="121" fill="url(#mediaBand)"/>
      </svg>
    </div>
    <h2>OUR BAND</h2>
    <p>Eque mi consectetuer mi a ultricies massa est sed nisl Class aptent taciti sociosqu ad litora torquent per conubia nostra per inceptos hymen</p>
    <a class="btn" href="#">LEARN MORE</a>
  </article>
  <article class="feature feature-videos">
    <div class="feature-media">
      <svg width="240" height="121" role="img" aria-label="Video still of the band performing on stage">
        <defs><linearGradient id="mediaVideo" x1="0" y1="0" x2="0" y2="1"><stop offset="0" stop-color="#141210"/><stop offset="1" stop-color="#2e2620"/></linearGradient></defs>
        <rect width="240" height="121" fill="url(#mediaVideo)"/>
        <circle cx="121" cy="63" r="20" fill="#ffffff"/>
        <polygon points="115,53 115,73 130,63" fill="#111111"/>
      </svg>
    </div>
    <h2>OUR VIDEOS</h2>
    <p>Eque mi consectetuer mi a ultricies massa est sed nisl Class aptent taciti sociosqu ad litora torquent per conubia nostra per inceptos hymen</p>
    <a class="btn" href="#">LEARN MORE</a>
  </article>
  <article class="feature feature-gallery">
    <div class="feature-media">
      <svg width="240" height="121" role="img" aria-label="Two smiling fans giving a thumbs up">
        <defs><linearGradient id="mediaGallery" x1="0" y1="0" x2="1" y2="0"><stop offset="0" stop-color="#2a2a30"/><stop offset=".6" stop-color="#5a4a48"/><stop offset="1" stop-color="#2a6ab8"/></linearGradient></defs>
        <rect width="240" height="121" fill="url(#mediaGallery)"/>
      </svg>
    </div>
    <h2>PHOTO GALLERY</h2>
    <p>Eque mi consectetuer mi a ultricies massa est sed nisl Class aptent taciti sociosqu ad litora torquent per conubia nostra per inceptos hymen</p>
    <a class="btn" href="#">LEARN MORE</a>
  </article>
</section>

<footer class="site-footer">
  <nav class="footer-nav">
    <a href="#">HOME</a><span class="sep">|</span><a href="#">BAND</a><span class="sep">|</span><a href="#">ON TOUR</a><span class="sep">|</span><a href="#">VIDEOS</a><span class="sep">|</span><a href="#">PICS</a><span class="sep">|</span><a href="#">DOWNLOADS</a><span class="sep">|</span><a href="#">KONTAKT</a>
  </nav>
  <p class="copyright">© 2015 Company Name&nbsp; All right reserved&nbsp; Term of Use</p>
  <div class="social">
    <a href="#">Chatterbox</a><a href="#">chirpnet</a><a href="#">clipwave</a><a href="#">tunedrift</a>
  </div>
</footer>
</body>
</html>
```